MBRDC redesign and update stationary bc envelopes.

Stationary, Envelopes, Brochures, Business Card. Need to add second surgeon and two other offices. I need everything to match. I am a oral & maxillofacial surgeon.
Additional surgeon and three office addresses.
Jae Min Park, DMD, MD, INC

3718 Silver Meadow Parkway
Cedar Bluff, CA 95410

642 Lorin Way, Suite 101
Linden Grove, CA. 95478

2317 Vale Street, Suite 105
Oakmere, CA. 95521
Updates

Logo design uploaded. Zapfino Extra/Adobe Garamond/Palatino are fonts used before. Not sure what is on exisiting stationary.

Target Market(s)

Referral dentist and sometimes patients. I am a oral & Maxillofacial surgeon.

Industry/Entity Type

Dental Clinic

Font styles to use
Serif
Script

Requirements
Must have
• Color of existing stationary. Update is possible.
Nice to have
• Conservative/modern
Should not have
• Playful

```html
<!DOCTYPE html>
<html lang="en">
<head>
<meta charset="utf-8">
<title>MBRDC Letterhead</title>
<link rel="stylesheet" href="https://fonts.googleapis.com/css2?family=EB+Garamond&family=PT+Serif:ital@0;1&display=swap">
<style>
  :root {
    --backdrop: #dedede;
    --paper: #f8f3e7;
    --green: #6a8f22;
    --brown: #664e40;
    --ink: #4a3a32;
    --cream: #f4ecdc;
    --sage: #c9d3a3;
  }
  * { margin: 0; padding: 0; box-sizing: border-box; }
  html, body {
    width: 1153px; height: 1200px; overflow: hidden;
    background: var(--backdrop);
  }
  .letterhead {
    position: absolute; left: 146px; top: 0;
    width: 861px; height: 1200px;
    background: var(--paper);
  }
  .brand {
    position: absolute; left: 54px; top: 118px;
    display: flex; align-items: center; gap: 14px;
  }
  .brand-dot {
    width: 46px; height: 46px; border-radius: 50%;
    background: var(--sage);
  }
  .brand-name {
    font-family: "EB Garamond", serif;
    font-size: 22px; line-height: 1.15;
    color: var(--green);
  }
  .contact {
    position: absolute; right: 63px; top: 84px;
    text-align: right;
    font-family: "PT Serif", serif;
    font-style: normal;
    color: var(--ink);
    font-size: 11px; line-height: 13.5px;
  }
  .surgeon {
    font-style: italic; color: var(--green);
    font-size: 14.5px; line-height: 19px;
  }
  .office { margin-top: 2px; }
  .office + .office { margin-top: 3px; }
  .phones { margin-top: 3px; }
  .label { font-style: italic; color: var(--green); }
  .footer-rule {
    position: absolute; left: 0; right: 0; top: 1150px;
    height: 3px; background: var(--green);
  }
  .footer-band {
    position: absolute; left: 0; right: 0; bottom: 0;
    height: 42px; background: var(--brown);
    display: flex; align-items: center; justify-content: center;
  }
  .web {
    font-family: "PT Serif", serif; font-style: italic;
    color: var(--cream); font-size: 19px; letter-spacing: 3.4px;
  }
</style>
</head>
<body>
  <main class="letterhead">
    <div class="brand">
      <span class="brand-dot"></span>
      <span class="brand-name">MBRDC<br>Oral &amp; Facial Surgery Center</span>
    </div>

    <address class="contact">
      <div class="surgeon">Thomas A. Merrill, DDS, Inc.</div>
      <div class="surgeon">Jae Min Park, DMD, MD, Inc.</div>
      <div class="office">3718 Silver Meadow Parkway<br>Cedar Bluff, CA 95410</div>
      <div class="office">642 Lorin Way, Suite 101<br>Linden Grove, CA. 95478</div>
      <div class="office">2317 Vale Street, Suite 105<br>Oakmere, CA. 95521</div>
      <div class="phones"><span class="label">Tel</span> 707.555.0142<br><span class="label">Fax</span> 707.555.0187</div>
      <div>drmerrill@silvermeadoworalsurgery.com</div>
    </address>

    <div class="footer-rule"></div>
    <footer class="footer-band">
      <span class="web">www.silvermeadoworalsurgery.com</span>
    </footer>
  </main>
</body>
</html>
```